Moravel Aesthetic Doctor

I require an elegant, luxurious looking business card for my aesthetic business. I am a doctor and that will set me aside from competitors. I am planning to provide home and spa based treatments to clients with high expectations. I have attached my logo.

```html
<!DOCTYPE html>
<html lang="en">
<head>
<meta charset="utf-8">
<title>Moravel Aesthetic Doctor – Business Card</title>
<link rel="stylesheet" href="https://fonts.googleapis.com/css2?family=Roboto:ital,wght@0,400;0,500;1,400&family=Raleway:wght@500&display=swap">
<style>
  :root {
    --backdrop: #e4e5e8;
    --card: #f3f3f4;
    --card-edge: #fbfbfb;
    --sky: #4da6dc;
    --sky-deep: #1e6aab;
    --sky-mid: #3b8fcf;
    --steel: #8c93a1;
    --ink: #2e2f33;
    --white: #ffffff;
  }
  * { margin: 0; padding: 0; box-sizing: border-box; }
  html, body { width: 1200px; height: 576px; overflow: hidden; }
  body {
    background: var(--backdrop);
    font-family: "Roboto", Arial, sans-serif;
    color: var(--ink);
    position: relative;
  }
  .card {
    position: absolute;
    width: 484px;
    height: 293px;
    border-radius: 11px;
    background: linear-gradient(180deg, var(--card-edge), var(--card));
    overflow: hidden;
  }
  .card--front { left: 82px; top: 139px; }
  .card--back { left: 602px; top: 138px; width: 481px; height: 291px; }

  /* brand lockup */
  .brand {
    position: absolute;
    display: flex;
    align-items: center;
    gap: 16px;
  }
  .brand__ring {
    width: 76px; height: 76px;
    border-radius: 50%;
    border: 2px solid var(--steel);
    flex: none;
  }
  .brand__name {
    font-family: "Roboto", Arial, sans-serif;
    font-weight: 400;
    color: var(--sky-mid);
    line-height: 1.05;
    letter-spacing: 0.06em;
    text-transform: uppercase;
  }
  .brand__name .line1 { display: block; font-size: 40px; }
  .brand__name .line2 { display: block; font-size: 17px; letter-spacing: 0.08em; }
  .card--front .brand { left: 86px; top: 60px; }
  .card--back .brand { left: 14px; top: 97px; }
  .card--back .brand__ring { width: 70px; height: 70px; }
  .card--back .brand__name .line1 { font-size: 36px; }
  .card--back .brand__name .line2 { font-size: 16px; }

  /* front */
  .services {
    position: absolute;
    left: 0; right: 0; top: 194px;
    text-align: center;
    font-size: 13px;
    line-height: 19px;
  }
  .services .sep { color: var(--sky); margin: 0 6px; }
  .tagline-band {
    position: absolute;
    left: 0; right: 0; top: 239px; height: 34px;
    background: linear-gradient(90deg, var(--sky-deep) 0%, var(--sky-mid) 55%, var(--sky-deep) 100%);
    color: var(--white);
    font-family: "Raleway", Arial, sans-serif;
    font-weight: 500;
    font-size: 12.5px;
    letter-spacing: 0.09em;
    display: flex; align-items: center; justify-content: center;
  }

  /* back */
  .wave { position: absolute; left: 0; top: 0; }
  .back-tagline {
    position: absolute;
    right: 26px; top: 22px;
    text-align: right;
    color: var(--white);
    font-size: 13px;
    line-height: 18px;
    letter-spacing: 0.02em;
  }
  .doctor { position: absolute; left: 26px; top: 186px; }
  .doctor__name { font-size: 19px; line-height: 22px; }
  .doctor__post { font-size: 9.5px; font-style: italic; color: var(--sky); margin-top: 3px; }
  .doctor__diploma { font-size: 12.5px; color: var(--sky); line-height: 16px; margin-top: 8px; }
  .contact {
    position: absolute;
    right: 27px; top: 181px;
    text-align: right;
    font-size: 12px;
  }
  .contact__row { display: flex; justify-content: flex-end; align-items: center; gap: 5px; height: 19px; }
  .contact__row--follow { margin-bottom: 10px; }
  .social-dot { width: 11px; height: 11px; border-radius: 50%; background: var(--sky); display: inline-block; }
  .contact svg { width: 10px; height: 10px; fill: var(--sky); }
</style>
</head>
<body>

<section class="card card--front">
  <div class="brand">
    <span class="brand__ring"></span>
    <span class="brand__name"><span class="line1">Moravel</span><span class="line2">Aesthetic Doctor</span></span>
  </div>
  <p class="services">
    Dermal Injectables<span class="sep">|</span>Plasma Facials<span class="sep">|</span>Microneedling<br>
    Skin Boosters<span class="sep">|</span>Excessive Sweating
  </p>
  <div class="tagline-band">HOME AND SPA BASED TREATMENTS</div>
</section>

<section class="card card--back">
  <svg class="wave" width="481" height="291" viewBox="0 0 481 291" aria-hidden="true">
    <path d="M0 0 H481 V72 C400 92 330 70 250 42 C170 16 80 22 0 52 Z" fill="var(--sky)"/>
    <path d="M0 48 C90 12 180 14 260 44 C340 74 410 88 481 74 V80 C410 96 330 82 250 54 C170 26 80 30 0 62 Z" fill="var(--steel)" opacity="0.85"/>
    <path d="M0 64 C90 30 190 30 270 62 C350 94 420 104 481 92 V96 C420 110 340 100 260 70 C180 40 90 42 0 72 Z" fill="var(--steel)" opacity="0.6"/>
  </svg>
  <p class="back-tagline">Home and Spa<br>Based Treatments</p>

  <div class="brand">
    <span class="brand__ring"></span>
    <span class="brand__name"><span class="line1">Moravel</span><span class="line2">Aesthetic Doctor</span></span>
  </div>

  <div class="doctor">
    <p class="doctor__name">Dr Elin Varga</p>
    <p class="doctor__post">MRCPCH MD</p>
    <p class="doctor__diploma">Australasian Diploma of<br>Aesthetic Medicine</p>
  </div>

  <div class="contact">
    <p class="contact__row contact__row--follow">Follow us on:&nbsp;<span class="social-dot"></span><span class="social-dot"></span></p>
    <p class="contact__row">0800 555 019
      <svg viewBox="0 0 24 24" aria-hidden="true"><path d="M6.6 10.8a15 15 0 0 0 6.6 6.6l2.2-2.2c.3-.3.7-.4 1-.2 1.1.4 2.3.6 3.6.6.6 0 1 .4 1 1V20c0 .6-.4 1-1 1A17 17 0 0 1 3 4c0-.6.4-1 1-1h3.5c.6 0 1 .4 1 1 0 1.3.2 2.5.6 3.6.1.3 0 .7-.2 1z"/></svg>
    </p>
    <p class="contact__row">elin@moravel.co.nz
      <svg viewBox="0 0 24 24" aria-hidden="true"><path d="M2 5h20v14H2z M3.5 6.5 12 13l8.5-6.5" /></svg>
    </p>
    <p class="contact__row">www.moravel.co.nz
      <svg viewBox="0 0 24 24" aria-hidden="true"><path d="M12 2a10 10 0 1 0 0 20 10 10 0 0 0 0-20zm0 2c1 1.2 1.8 3 2.1 5H9.9C10.2 7 11 5.2 12 4zM4.3 11h3.6a15 15 0 0 0 0 2H4.3a8 8 0 0 1 0-2zm5.6 0h4.2a13 13 0 0 1 0 2H9.9a13 13 0 0 1 0-2zm6.2 0h3.6a8 8 0 0 1 0 2h-3.6a15 15 0 0 0 0-2zM9.9 15h4.2c-.3 2-1.1 3.8-2.1 5-1-1.2-1.8-3-2.1-5z"/></svg>
    </p>
  </div>
</section>

</body>
</html>
```